Awsome new website

We are a Fencing Contracting company in Melbourne Australia. We supply and install Timer and Steel boundary fences as well as Pool fencing (e.g. glass, tubular steel). We also manufacture and install swing and sliding gates.

We want a new website that is a modern business website.
We are targeting domestic and business clients.
The design should compliment our logo and company name.
The website needs to be easy to update.

Some specifics we want.
Menu - Main menu at top of page and smaller footer menu (to add different menu items)
Slider - Main page to have a slider on it that's easy for us to add and remove slides.
Call to action - all pages to have a "call to action" logo or icon that attracts attention (see file "call_to_action.pdf)
Instant quote - we have a online quote page we need a distinctive logo or icon to redirect to this page.
Main page to have a product /Service guide (see file "website_idea.jpg")
Main page to have widgets or quick link to
o why choose us
o Brochures
o Gallery

Have a Gallery page formatted with different category galleries. e.g. Timber, Glass, Feature
Maintain the current link to our staff page with password, (link in footer menu)

Hopefully that covers everything.
Our current website is www.tallgumfencing.com.au to have a look at the current site.
regards Doug

• Turn off blogging as we don’t want 100’s of comments from spammers to delete

We would like to implement the Portalio plugin (see "http://portalio-plug.net/" ), but this can be done after the new Theme has been implemented.

```html
<!DOCTYPE html>
<html lang="en">
<head>
<meta charset="utf-8">
<title>Tall Gum Fencing</title>
<link href="https://fonts.googleapis.com/css2?family=Source+Sans+3:wght@400;600;700&display=swap" rel="stylesheet">
<style>
:root{
  --red:#a31c16;
  --red-dark:#861410;
  --heading:#8f1b15;
  --yellow:#ffc93a;
  --text:#555;
  --muted:#777;
  --panel:#f4f4f4;
  --band:#ececec;
  --footer:#2c2c2c;
}
*{margin:0;padding:0;box-sizing:border-box}
html,body{width:979px;height:1200px;overflow:hidden;background:#fff}
body{font-family:"Source Sans 3",Arial,sans-serif;color:var(--text);position:relative}
.abs{position:absolute}

.header{top:0;left:0;width:979px;height:99px}
.brand{left:83px;top:22px;display:flex;align-items:center;gap:8px}
.brand-mark{width:20px;height:20px;background:var(--red)}
.brand-name{font-size:24px;font-weight:700;color:var(--red);line-height:1}
.brand-tag{left:83px;top:54px;font-size:10px;font-weight:600;color:var(--red);letter-spacing:.3px;text-transform:uppercase}
.call-badge{left:760px;top:33px}

.nav{top:99px;left:0;width:979px;height:39px;background:linear-gradient(#c2271f,#8e1511);border-bottom:2px solid #6d0f0c}
.nav ul{list-style:none;display:flex;position:absolute;left:83px;top:0;height:37px}
.nav li{height:37px;line-height:37px;padding:0 17px;color:#fff;font-size:13.5px;font-weight:600;text-transform:uppercase;border-right:1px solid #7d1310;position:relative}
.nav li.active{background:var(--red-dark);border-left:1px solid #7d1310}
.nav li.active::after{content:"";position:absolute;left:50%;bottom:0;margin-left:-5px;border:5px solid transparent;border-bottom-color:#ddd}
.nav .phone{position:absolute;left:786px;top:0;line-height:37px;color:var(--yellow);font-size:19px;font-weight:700}

.slider{top:138px;left:0;width:979px;height:414px;background:linear-gradient(180deg,#7c9446 0%,#5e7a2e 40%,#8b8a78 70%,#4f5a34 100%)}
.caption{top:498px;left:0;width:979px;height:54px;background:rgba(20,20,20,.78)}
.caption p{position:absolute;left:82px;top:14px;color:#fff;font-size:18.5px}
.dots{position:absolute;right:82px;top:21px;display:flex;gap:7px}
.dots span{width:12px;height:12px;border-radius:50%;background:#bbb;border:1px solid #888}
.dots span:first-child{background:#333}

h1,h2{color:var(--heading);font-weight:600}
.welcome{left:83px;top:576px;width:548px}
.welcome h1{font-size:23px;line-height:28px;margin-bottom:8px}
.welcome p{font-size:12.3px;line-height:20.4px;text-align:justify}
.thumbs{left:84px;top:709px;display:flex;gap:8px}
.thumb{width:177px;height:97px}
.t1{background:linear-gradient(#7a5b46,#6d8d3e 55%,#e8ecea 85%)}
.t2{background:linear-gradient(#3c6a2c,#4f4438 50%,#6c9a3d)}
.t3{background:linear-gradient(#2d5a3a,#8aa89a 45%,#4c9cc4 75%,#a59a86)}
.rule{left:86px;top:821px;width:544px;height:1px;background:#ddd}

.services{left:83px;top:836px;width:548px}
.services h2{font-size:19.5px;margin-bottom:8px}
.services p{font-size:11px;line-height:20.5px;color:var(--muted)}
.svc-list{left:86px;top:942px;display:grid;grid-template-columns:176px 127px 170px;row-gap:10px}
.svc-list span{font-size:11px;color:var(--muted);display:flex;align-items:center;gap:9px;height:16px}
.svc-list span::before{content:"";width:9px;height:9px;border-radius:50%;background:#888;box-shadow:inset 0 0 0 2px #ccc}

.cta{left:660px;width:238px;height:60px;border-radius:3px;display:flex;align-items:center;gap:16px;padding-left:22px;color:var(--yellow);font-size:21px;font-weight:600;white-space:nowrap}
.cta-quote{top:581px;background:linear-gradient(#c8342b,#9a1812);border:1px solid #7d1310}
.cta-brochure{top:645px;background:linear-gradient(#5a5a5a,#333);border:1px solid #222}
.cta-icon{width:28px;height:32px;background:#f2f2f2;border-radius:2px;box-shadow:1px 1px 2px rgba(0,0,0,.4);flex:none}

.why-title{left:663px;top:723px;font-size:19.5px}
.why{left:660px;top:755px;width:238px;height:255px;background:var(--panel);border-top:1px solid #e2e2e2;border-bottom:1px solid #ddd;padding:16px 8px 0 11px}
.why p{font-size:12px;line-height:19px;text-align:justify;margin-bottom:7px}
.why a{color:var(--red);text-decoration:none}
.guarantee{left:674px;top:918px;display:flex;align-items:center;gap:14px}
.seal{width:76px;height:76px;border-radius:50%;background:radial-gradient(#f7d35c,#d79a1c);border:3px solid #c48614}
.guarantee p{font-size:16.5px;line-height:22px;color:#333}

.info-band{top:1038px;left:0;width:979px;height:78px;background:var(--band)}
.info{position:absolute;top:20px;display:flex;align-items:center;gap:12px;font-size:12px;line-height:19px;color:#666}
.info svg{flex:none}

.footer{top:1116px;left:0;width:979px;height:84px;background:var(--footer)}
.footer-menu{position:absolute;left:83px;top:18px;font-size:11.5px;color:#ccc;display:flex}
.footer-menu span{padding:0 9px;border-left:1px solid #999;line-height:12px}
.footer-menu span:first-child{padding-left:0;border-left:0}
.copyright{position:absolute;left:83px;top:51px;font-size:11px;color:#bbb}
.social{position:absolute;left:791px;top:31px;display:flex;gap:8px}
.social span{width:21px;height:21px;border-radius:50%;background:#777}
</style>
</head>
<body>

<header class="abs header">
  <div class="abs brand"><span class="brand-mark"></span><span class="brand-name">Tall Gum Fencing</span></div>
  <div class="abs brand-tag">Built straight, built to last</div>
  <svg class="abs call-badge" width="144" height="66" viewBox="0 0 144 66" aria-label="Call us">
    <path d="M6 6 L138 2 L140 46 L104 50 L112 64 L90 50 L10 54 Z" fill="#b8211a" stroke="#8a150f" stroke-width="1.5"/>
    <path d="M26 16 q-6 4 -2 14 q5 10 12 10 l3 -5 l-5 -4 l-3 3 q-5 -3 -6 -9 l3 -2 l-2 -6 z" fill="#ffc93a"/>
    <text x="44" y="36" fill="#ffc93a" font-family="Source Sans 3, Arial, sans-serif" font-size="21" font-weight="700">CALL US</text>
  </svg>
</header>

<nav class="abs nav">
  <ul>
    <li class="active">Home</li>
    <li>Steel Panel</li>
    <li>Instant Quote</li>
    <li>Gallery</li>
    <li>Products &amp; Services</li>
    <li>Contact Us</li>
  </ul>
  <div class="phone">03 9047 2261</div>
</nav>

<section class="abs slider" role="img" aria-label="Slide photo: cattle grazing in a paddock behind an old timber and steel farm gate"></section>
<div class="abs caption">
  <p>Phasellus erat felis, scelerisque a rutrum vitae, malesuada id erat</p>
  <div class="dots"><span></span><span></span><span></span><span></span></div>
</div>

<section class="abs welcome">
  <h1>Welcome to Tall Gum Fencing</h1>
  <p>Donec tincidunt gravida mauris at mollis. Nulla consectetur magna et purus porttitor, nec sollicitudin felis bibendum. Pellentesque quis malesuada risus. Vivamus vehicula feugiat porttitor. Sed pellentesque ullamcorper volutpat. Praesent volutpat augue ac sapien egestas, feugiat feugiat augue convallis. Aenean neque sapien, mollis eget auctor at, lacinia nec nulla.</p>
</section>
<div class="abs thumbs">
  <div class="thumb t1" role="img" aria-label="White picket garden fence in front of a brick house"></div>
  <div class="thumb t2" role="img" aria-label="Black tubular steel fence and gate on a lawn"></div>
  <div class="thumb t3" role="img" aria-label="Glass pool fence beside a swimming pool"></div>
</div>
<div class="abs rule"></div>

<section class="abs services">
  <h2>Tall Gum Fencing Services</h2>
  <p>We offer a 12 month workmanshhttp://tallgumfencing.com.au/images/bt-arise/aboutus.jpgip warranty on our fences and wll clean the site for free of any debris from the fence construction upon completion of the job. We can offer this workmanship warranty because of our work practices, these include</p>
</section>
<div class="abs svc-list">
  <span>Bathroom Remodeling</span><span>Tile &amp; Flooring</span><span>Genral Home Maintenance</span>
  <span>Attic &amp; Garage Finishing</span><span>Decks</span><span>Painting &amp; Wall Treatments</span>
  <span>Carpentry</span><span>Fences</span><span>Drywall Install</span>
</div>

<div class="abs cta cta-quote"><span class="cta-icon"></span>Get QuickQuote</div>
<div class="abs cta cta-brochure"><span class="cta-icon"></span>Get Our Broucher</div>

<h2 class="abs why-title">Why Choose us?</h2>
<aside class="abs why">
  <p>Nunc bibendum nunc eget nisl molestie, eu dictum dui imperdiet. Nam a augue ac ligula pulvinar rhoncus.</p>
  <p>Nunc vitae congue lorem. Nunc ut diam sed velit sollicitudin ullamcorper in a libero. Duis iaculis vulputate nisl, vel tristique sapien scelerisque eget. <a href="#">More</a></p>
</aside>
<div class="abs guarantee"><div class="seal"></div><p>100% Satisfaction<br>Guarantee</p></div>

<section class="abs info-band">
  <div class="info" style="left:124px">
    <svg width="20" height="24" viewBox="0 0 20 24"><rect x="1" y="3" width="18" height="20" fill="none" stroke="#888" stroke-width="2"/><rect x="6" y="0" width="8" height="14" fill="#888"/></svg>
    <div>55, Building name, Street name<br>City - Zipcode</div>
  </div>
  <div class="info" style="left:390px">
    <svg width="24" height="24" viewBox="0 0 24 24"><path d="M3 3 q-3 8 6 16 q8 6 13 2 l-4 -5 l-4 2 q-5 -3 -7 -8 l3 -3 z" fill="#888"/></svg>
    <div>Phone &nbsp;&nbsp;: 503.418.6620<br>Toll Free: 888.517.2046</div>
  </div>
  <div class="info" style="left:642px;top:28px">
    <svg width="23" height="16" viewBox="0 0 23 16"><rect width="23" height="16" fill="#888"/><path d="M0 0 L11.5 9 L23 0" fill="none" stroke="#eee" stroke-width="1.5"/></svg>
    <div>E-mail : info@tallgumfencing.com.au</div>
  </div>
</section>

<footer class="abs footer">
  <div class="footer-menu"><span>Home</span><span>Steel Panel</span><span>Instant Quote</span><span>Gallery</span><span>Products &amp; Services</span><span>Contact us</span></div>
  <div class="copyright">Copyright &copy; 2013 &nbsp; Tall Gum Fencing. &nbsp; All rights reserved.</div>
  <div class="social"><span></span><span></span><span></span><span></span></div>
</footer>

</body>
</html>
```